MBR - Stationery Design Project

We need stationery based on our logo.

Company info :
Cabinet Voisard & Associés
Société à responsabilité limitée au capital de 200.000 FCFP
RCS Papeete 27586K - Numéro tahiti K73962
Centre d’affaires OPALE - Rue Gaston Perrin
BP 61384 MAHU POTE - 98752 Papeete
Tahiti - Polynésie française
Tél : +689 40 73 16 48
Fax : +689 40 39 64 91

Industry/Entity Type

It Company

Font styles to use
Sans Serif

```html
<!DOCTYPE html>
<html lang="fr">
<head>
<meta charset="utf-8">
<title>MBR – Papier à en-tête</title>
<link rel="stylesheet" href="https://fonts.googleapis.com/css2?family=Questrial&display=swap">
<style>
  :root {
    --backdrop: #ececec;
    --paper: #fbfbfb;
    --navy: #2b3a5c;
    --slate: #8e9a9b;
    --watermark: #f0f1f1;
    --footer-text: #6f7778;
  }
  * { margin: 0; padding: 0; box-sizing: border-box; }
  html, body {
    width: 1200px;
    height: 1000px;
    overflow: hidden;
    background: var(--backdrop);
    font-family: "Questrial", sans-serif;
  }
  .letterhead {
    position: absolute;
    left: 282px;
    top: 50px;
    width: 636px;
    height: 900px;
    background: var(--paper);
    box-shadow: 0 2px 10px rgba(0,0,0,0.08);
  }
  .brand {
    position: absolute;
    left: 44px;
    top: 40px;
    color: var(--navy);
  }
  .brand-name {
    font-size: 52px;
    line-height: 1;
    letter-spacing: 1px;
  }
  .brand-company {
    font-size: 12px;
    margin-top: 2px;
    letter-spacing: 0.2px;
  }
  .brand-tagline {
    font-size: 6.5px;
    margin-top: 2px;
    letter-spacing: 0.6px;
    color: var(--slate);
  }
  .watermark {
    position: absolute;
    left: 0;
    right: 0;
    top: 300px;
    text-align: center;
    font-size: 190px;
    line-height: 1;
    color: var(--watermark);
    letter-spacing: 4px;
    user-select: none;
  }
  .legal {
    position: absolute;
    left: 28px;
    right: 28px;
    bottom: 36px;
    font-size: 6.4px;
    line-height: 1.6;
    color: var(--footer-text);
    text-align: right;
  }
  .footer-band {
    position: absolute;
    left: 0;
    bottom: 16px;
    width: 636px;
    height: 8px;
    display: block;
  }
</style>
</head>
<body>
  <main class="letterhead">
    <header class="brand">
      <div class="brand-name">MBR</div>
      <div class="brand-company">Cabinet Voisard &amp; Associés</div>
      <div class="brand-tagline">Expertise · Conseil · Audit · Gestion</div>
    </header>

    <div class="watermark" aria-hidden="true">MBR</div>

    <footer class="legal">
      <p>Cabinet Voisard &amp; Associés - Société à responsabilité limitée au capital de 200.000 FCFP - RCS Papeete 27586K - Numéro tahiti K73962</p>
      <p>Centre d’affaires OPALE - Rue Gaston Perrin - BP 61384 MAHU POTE - 98752 Papeete Tahiti - Polynésie française &nbsp;|&nbsp; Tél : +689 40 73 16 48 &nbsp;|&nbsp; Fax : +689 40 39 64 91</p>
    </footer>

    <svg class="footer-band" viewBox="0 0 636 8" aria-hidden="true">
      <polygon points="0,0 412,0 406,8 0,8" fill="var(--navy)"/>
      <polygon points="418,0 636,0 636,8 412,8" fill="var(--slate)"/>
    </svg>
  </main>
</body>
</html>
```